BLS Business Card 2018

Larkmere Chiropractic. We have two locations that we want to advertise on the same card. Brightvale OrthoCore campus address: 3815 Pellham Dr., Suite 240, Ashby Ridge, ST 39417. Carrow Falls address: 246 Willowmere Dr., Building D., Carrow Falls, ST 39284. website: www.drlarkmere-example.com. o:(601)555-0147 f:(601)555-0183

Target Market(s)

Health care decision makers: primary care doctors and mothers

Contact Information for Business Card

I have no idea; up for any suggestions and I'd do much better picking from examples versus describing what I'm looking for. We are in a very high end location and would like the cards to look really sharp.

Requirements
Must have
• My name, Martin R Belvane, D.C.

```html
<!DOCTYPE html>
<html lang="en">
<head>
<meta charset="utf-8">
<title>Larkmere Chiropractic Business Card</title>
<link rel="stylesheet" href="https://fonts.googleapis.com/css2?family=Cinzel:wght@400;500&family=Open+Sans:wght@400;600&display=swap">
<style>
  :root {
    --backdrop: #8c8c8c;
    --card-light: #efefef;
    --card-dark: #000000;
    --ink: #111111;
    --rule: #c4c4c4;
    --paper-white: #ffffff;
    --figure-tone: #141414;
  }
  * { margin: 0; padding: 0; box-sizing: border-box; }
  html, body {
    width: 1200px; height: 1200px; overflow: hidden;
    background: var(--backdrop);
  }
  .canvas { position: relative; width: 1200px; height: 1200px; }

  .card { position: absolute; top: 310px; height: 593px; overflow: hidden; }
  .card--front { left: 234px; width: 364px; background: var(--card-light); color: var(--ink); }
  .card--back  { left: 627px; width: 369px; background: var(--card-dark); color: var(--paper-white); }

  .brand { position: absolute; font-family: "Cinzel", serif; font-weight: 400; line-height: 1; }
  .brand__name { display: block; }
  .brand__sub { display: block; }

  .card--front .brand { left: 108px; top: 124px; color: var(--ink); }
  .card--front .brand__name { font-size: 35px; letter-spacing: 0.5px; }
  .card--front .brand__sub { font-size: 23px; margin-top: 3px; letter-spacing: 0.6px; }

  .contact {
    position: absolute; left: 0; right: 0; top: 278px;
    text-align: center; font-family: "Open Sans", sans-serif; font-size: 15.5px; line-height: 21.5px;
  }
  .contact__person {
    font-family: "Cinzel", serif; font-size: 19px; letter-spacing: 0.8px; line-height: 26px;
    padding-bottom: 8px;
  }
  .contact__rule { width: 256px; height: 1px; background: var(--rule); margin: 0 auto; }
  .contact__group { padding: 6px 0 8px; }
  .contact__label { font-weight: 600; }
  .contact__heading { font-weight: 600; text-transform: uppercase; letter-spacing: 0.3px; }

  .back-figure {
    position: absolute; left: 0; top: 30px; width: 369px; height: 460px;
    background: radial-gradient(ellipse 50% 50% at 50% 50%, var(--figure-tone), rgba(0,0,0,0) 100%);
  }
  .card--back .brand { left: 46px; top: 477px; color: var(--paper-white); }
  .card--back .brand__name { font-size: 38px; letter-spacing: 0.5px; }
  .card--back .brand__sub { font-size: 25px; margin-top: 3px; letter-spacing: 0.6px; }
</style>
</head>
<body>
<main class="canvas">
  <section class="card card--front">
    <div class="brand">
      <span class="brand__name">LARKMERE</span>
      <span class="brand__sub">Chiropractic</span>
    </div>
    <div class="contact">
      <p class="contact__person">MARTIN R BELVANE, D.C.</p>
      <div class="contact__rule"></div>
      <div class="contact__group">
        <p><span class="contact__label">P:</span> (555)555-0147</p>
        <p><span class="contact__label">F:</span> (555)555-0183</p>
        <p>www.drlarkmere-example.com</p>
      </div>
      <div class="contact__rule"></div>
      <div class="contact__group">
        <p class="contact__heading">Brightvale OrthoCore Campus</p>
        <p>3815 Pellham Dr., Suite 240</p>
        <p>Ashby Ridge, ST 39417.</p>
      </div>
      <div class="contact__rule"></div>
      <div class="contact__group">
        <p class="contact__heading">Carrow Falls</p>
        <p>246 Willowmere Dr., Building D.,</p>
        <p>Carrow Falls, ST 39284.</p>
      </div>
    </div>
  </section>

  <section class="card card--back">
    <div class="back-figure" role="img" aria-label="Faint line illustration of a human back and torso"></div>
    <div class="brand">
      <span class="brand__name">LARKMERE</span>
      <span class="brand__sub">Chiropractic</span>
    </div>
  </section>
</main>
</body>
</html>
```